Management consulting Company in the electronic payment ecosystem needs a Website

We need to have a "showcase" style website that contains the key message that our company is able to provide management consulting in the world of payment systems. Our mission is to assist our clients in reviewing their sales, purchasing, operation and IT processes and to support them in identifying the best solution in the use of payment systems.

```html
<!DOCTYPE html>
<html lang="en">
<head>
<meta charset="utf-8">
<title>Tally Consulting — Pay Management Consulting</title>
<link href="https://fonts.googleapis.com/css2?family=Prata&family=Lato:ital,wght@0,400;0,700;0,900;1,700&display=swap" rel="stylesheet">
<style>
:root{
  --navy:#18265a;
  --navy-deep:#1c2d66;
  --orange:#e8703c;
  --orange-light:#f0865a;
  --ink:#2b2b35;
  --muted:#55586a;
  --sky:#eef4fd;
  --sky-2:#dce8fb;
  --line:#e3e7ef;
  --white:#ffffff;
}
*{margin:0;padding:0;box-sizing:border-box}
html,body{width:1200px;height:5181px;overflow:hidden}
body{position:relative;background:var(--white);font-family:'Lato',sans-serif;color:var(--ink)}
.abs{position:absolute}
.serif{font-family:'Prata',serif;font-weight:400}
.btn{position:absolute;display:flex;align-items:center;justify-content:center;font:900 13px 'Lato',sans-serif;letter-spacing:.5px;text-transform:uppercase}
.btn-fill{background:var(--orange);color:var(--white);box-shadow:0 4px 10px rgba(232,112,60,.35)}
.btn-line{border:2px solid var(--navy);color:var(--navy);background:var(--white);border-radius:3px}
.brand{display:flex;align-items:center;gap:10px}
.brand-dot{width:74px;height:74px;border-radius:50%;border:12px solid var(--navy)}
.brand-name{font-family:'Prata',serif;color:var(--navy);font-size:78px;line-height:1}

/* hero */
.hero{left:0;top:0;width:1200px;height:770px;background:linear-gradient(180deg,#f3f7fe 0%,var(--sky) 100%);overflow:hidden}
.hero-blob{left:-120px;top:80px;width:760px;height:700px;border-radius:50%;background:rgba(210,225,248,.55)}
.contact-bar{left:512px;top:36px;display:flex;align-items:center;gap:16px;font-size:16px;color:var(--ink)}
.contact-bar .ico{color:var(--orange)}
.social{display:flex;gap:5px}
.social span{width:24px;height:24px;border-radius:50%;border:2px solid var(--orange)}
.nav-rule{left:500px;top:88px;width:558px;height:2px;background:var(--orange)}
.nav{left:502px;top:107px;display:flex;gap:33px;font-family:'Prata',serif;font-size:17px;color:var(--navy)}
.nav .active{color:var(--orange)}
.hero-title{left:144px;top:234px;font-size:50px;line-height:1.3;color:var(--navy)}
.hero-text{left:144px;top:378px;width:390px;font-size:17px;line-height:1.5;color:var(--ink)}
.hero-art{left:560px;top:180px;width:620px;height:530px;border-radius:46% 40% 44% 50%;background:radial-gradient(circle at 45% 55%,#b9cdf5 0%,#8fb0ee 40%,#d6e2fa 75%,transparent 76%)}
.dots{left:560px;top:700px;display:flex;gap:8px;align-items:center}
.dots span{width:10px;height:10px;border-radius:50%;background:var(--navy)}
.dots .on{width:16px;height:16px;background:none;border:3px solid var(--navy);box-shadow:inset 0 0 0 3px var(--white),inset 0 0 0 8px var(--navy)}

/* headings */
.sec-title{position:absolute;left:0;width:1200px;text-align:center;font-family:'Prata',serif;font-size:35px;color:var(--navy)}
.sec-rule{position:absolute;left:555px;width:90px;height:3px;background:var(--navy)}

/* mission */
.mission-text{left:245px;top:948px;width:710px;text-align:center;font-size:17.5px;line-height:1.5}
.m-card{position:absolute;width:288px;background:var(--white);border:1px solid var(--line);text-align:center}
.m-card.raise{box-shadow:0 10px 26px rgba(24,38,90,.15);border-color:transparent}
.m-icon{width:122px;height:122px;border-radius:50%;margin:28px auto 0;border:3px solid var(--navy);border-left-width:14px;display:flex;align-items:center;justify-content:center}
.m-card h3{font-family:'Prata',serif;font-weight:400;font-size:20px;color:var(--navy);margin-top:14px}
.m-card p{font-size:14px;line-height:1.55;color:var(--muted);padding:0 30px;margin-top:12px}
.m-card .btn{position:relative;margin:18px auto 0;width:138px;height:38px}

/* about */
.about-art{left:148px;top:1590px;width:388px;height:412px;border-radius:50%;background:radial-gradient(circle at 50% 45%,#cdb8a8 0%,#6e5b52 55%,#2f2a2c 100%);overflow:hidden}
.about-title{left:596px;top:1616px;font-size:34px;color:var(--navy)}
.about-text{left:596px;top:1714px;width:462px;font-size:15.5px;line-height:1.5;color:var(--muted)}

/* stats */
.stats{left:0;top:2090px;width:1200px;height:476px;background:linear-gradient(180deg,#eef1f8 0%,#e4e8f0 100%);overflow:hidden}
.stats-people{left:90px;top:2360px;width:1020px;height:206px;background:linear-gradient(90deg,#8a7a6e,#b79a86,#9da6b6,#6f7e94,#c2a594,#7b6c63)}
.stat{position:absolute;width:188px;height:188px;border-radius:50%;background:var(--white);border:8px solid var(--navy);display:flex;flex-direction:column;align-items:center;justify-content:center;color:var(--navy)}
.stat b{font:900 34px 'Lato',sans-serif}
.stat small{font-size:17px;text-align:center;line-height:1.15}

/* what we do */
.wwd{left:0;top:2566px;width:1200px;height:858px;background:linear-gradient(135deg,var(--orange-light),var(--orange) 60%,#e26a36)}
.w-card{position:absolute;width:446px;height:274px;background:var(--white);overflow:hidden}
.w-copy{position:absolute;left:32px;top:28px;width:220px}
.w-copy h4{font-family:'Prata',serif;font-weight:400;font-size:18px;color:var(--navy)}
.w-copy p{font-size:14.5px;line-height:1.38;color:var(--muted);margin-top:14px}
.w-card .btn{left:32px;top:206px;width:128px;height:38px}
.w-photo{position:absolute;right:0;top:0;width:184px;height:274px;background:linear-gradient(160deg,#3a4d84,#243463 70%,#1b2755)}
.w-ring{position:absolute;left:42px;top:86px;width:100px;height:100px;border-radius:50%;border:2px solid rgba(255,255,255,.9)}

/* news */
.n-card{position:absolute;width:286px;background:var(--white);box-shadow:0 6px 20px rgba(24,38,90,.12)}
.n-photo{height:238px;margin:4px}
.n-date{font:italic 700 14px 'Lato',sans-serif;color:var(--navy-deep);margin:12px 20px 0;display:flex;gap:6px;align-items:center}
.n-card h5{font:900 14.5px 'Lato',sans-serif;color:var(--navy);text-transform:uppercase;line-height:1.55;margin:14px 20px 0}
.n-card p{font-size:14.5px;line-height:1.35;color:var(--muted);margin:16px 20px 28px}

/* cta */
.cta{left:0;top:4130px;width:1200px;height:520px}
.cta-title{left:0;top:4210px;width:1200px;text-align:center;font-size:35px;color:var(--white)}
.cta-text{left:222px;top:4306px;width:756px;text-align:center;font-size:16px;line-height:1.5;color:var(--white)}

/* footer */
.footer{left:0;top:4560px;width:1200px;height:621px;background:#f6f8fc}
.f-about{left:137px;top:4762px;width:190px;font-size:15px;line-height:1.3;color:var(--ink)}
.f-head{font:900 16px 'Lato',sans-serif;color:var(--ink);text-transform:uppercase;letter-spacing:.3px}
.field{position:absolute;left:382px;width:274px;height:46px;border:1px solid #d5d9e2;background:var(--white);font-size:14px;color:var(--muted);padding:14px 18px}
.f-contact{left:700px;top:4736px;width:230px;font-size:14px;line-height:1.4;color:var(--ink)}
.f-row{display:flex;gap:14px;margin-bottom:12px}
.f-links{left:950px;top:4736px;font-size:14px;line-height:27px;color:var(--ink)}
.copyright{left:0;top:5098px;width:1200px;text-align:center;font-size:15px;color:var(--ink)}
.copy-rule{left:0;top:5070px;width:1200px;height:1px;background:var(--line)}
</style>
</head>
<body>

<!-- HERO -->
<section class="abs hero">
  <div class="abs hero-blob"></div>
  <div class="abs brand" style="left:144px;top:30px">
    <span class="brand-dot"></span><span class="brand-name">Tally</span>
  </div>
  <div class="abs contact-bar">
    <span class="ico">&#9990;</span><span>555 0142 2200</span>
    <span class="ico" style="margin-left:8px">&#9993;</span><span>hello@tallyconsult.example</span>
    <span class="social"><span></span><span></span><span></span></span>
  </div>
  <div class="abs nav-rule"></div>
  <nav class="abs nav"><span class="active">Home</span><span>About Us</span><span>Our Services</span><span>Resources</span><span>Contact Us</span></nav>
  <h1 class="abs serif hero-title">Pay Management<br>Consulting</h1>
  <p class="abs hero-text">Sed ut perspiciatis unde omnis iste natus voluptatem accusantium doloremque launtium, totam rem aperiam, eaque ipsa quae ab illo inventore veritatis et quasi architecto beatae vitae dicta sunt explicabo.</p>
  <div class="btn btn-fill" style="left:144px;top:532px;width:160px;height:44px">Learn More</div>
  <div class="abs hero-art" role="img" aria-label="Illustration of two consultants working at a round desk with charts and a laptop"></div>
  <div class="abs dots"><span class="on"></span><span></span><span></span><span></span></div>
</section>

<!-- MISSION -->
<h2 class="sec-title" style="top:850px">Our Mission</h2>
<div class="sec-rule" style="top:916px"></div>
<p class="abs mission-text">Our mission is to assist our clients in reviewing their sales, purchasing, operation and IT processes and to support them in identifying the best solution in the use of payment systems</p>

<div class="m-card" style="left:143px;top:1062px;height:414px">
  <div class="m-icon"><svg width="56" height="56" viewBox="0 0 56 56" fill="none" stroke="#18265a" stroke-width="3"><path d="M4 10h8l6 26h26l6-18H16"/><circle cx="22" cy="46" r="4"/><circle cx="40" cy="46" r="4"/></svg></div>
  <h3>Purchasing</h3>
  <p>Sed ut perspiciatis unde omnis iste natus error sit voluptatem accusantium doloremque dantium, totam rem aperiam, eaque ipsa quae ab illo inventore veritatis et quasi architecto</p>
  <div class="btn btn-line">Learn More</div>
</div>
<div class="m-card raise" style="left:456px;top:1086px;height:414px">
  <div class="m-icon"><svg width="56" height="56" viewBox="0 0 56 56" fill="none" stroke="#18265a" stroke-width="3"><circle cx="28" cy="20" r="10"/><path d="M10 52c0-10 8-16 18-16s18 6 18 16"/><path d="M16 20a12 12 0 0 1 24 0"/></svg></div>
  <h3>Operation</h3>
  <p>Sed ut perspiciatis unde omnis iste natus error sit voluptatem accusantium doloremque dantium, totam rem aperiam, eaque ipsa quae ab illo inventore veritatis et quasi architecto</p>
  <div class="btn btn-line">Learn More</div>
</div>
<div class="m-card" style="left:767px;top:1062px;height:414px">
  <div class="m-icon"><svg width="56" height="56" viewBox="0 0 56 56" fill="none" stroke="#18265a" stroke-width="3"><rect x="20" y="6" width="16" height="12"/><rect x="4" y="38" width="14" height="12"/><rect x="21" y="38" width="14" height="12"/><rect x="38" y="38" width="14" height="12"/><path d="M28 18v10M11 38v-10h34v10M28 28v10"/></svg></div>
  <h3>It Processes</h3>
  <p>Sed ut perspiciatis unde omnis iste natus error sit voluptatem accusantium doloremque dantium, totam rem aperiam, eaque ipsa quae ab illo inventore veritatis et quasi architecto</p>
  <div class="btn btn-line">Learn More</div>
</div>

<!-- ABOUT -->
<div class="abs about-art" role="img" aria-label="Circular photo collage of a smiling businesswoman and a colleague using a tablet"></div>
<h2 class="abs serif about-title">About Tally Consulting</h2>
<p class="abs about-text">Sed ut perspiciatis unde omnis iste natus error sit voluptatem accusantium doloremque laudantium, totam rem aperiam, eaque ipsa quae ab illo inventore veritatis et quasi architecto beatae vitae dicta sunt explicabo. Nemo enim ipsam voluptatem quia voluptas sit aspernatur aut odit aut fugit, sed quia cquuntur magni dolores eos qui ratione voluptatem sequi nesciunt. Neque porro quisquam est, qui dolorem ipsum quia dolor sit amet, consectetur, adipisci velit</p>
<div class="btn btn-line" style="left:596px;top:1924px;width:146px;height:40px">Learn More</div>

<!-- STATS -->
<section class="abs stats"></section>
<div class="abs stats-people" role="img" aria-label="Photo of six smiling professionals sitting together with laptops"></div>
<div class="stat" style="left:258px;top:2152px;border-left-color:var(--orange);border-bottom-color:var(--orange)">
  <svg width="34" height="34" viewBox="0 0 34 34"><circle cx="17" cy="17" r="16" fill="#18265a"/><circle cx="17" cy="13" r="5" fill="#fff"/><path d="M8 27c2-6 16-6 18 0" fill="#fff"/></svg>
  <b>500 +</b><small>Members</small>
</div>
<div class="stat" style="left:505px;top:2142px">
  <svg width="34" height="34" viewBox="0 0 34 34"><path d="M32 2L2 15l12 4 4 12z" fill="#18265a"/></svg>
  <b>200 +</b><small>Active<br>innovators</small>
</div>
<div class="stat" style="left:752px;top:2152px;border-right-color:var(--orange);border-top-color:var(--orange)">
  <svg width="44" height="30" viewBox="0 0 44 30" fill="#18265a"><circle cx="22" cy="8" r="6"/><circle cx="9" cy="10" r="4.5"/><circle cx="35" cy="10" r="4.5"/><path d="M12 28c0-9 20-9 20 0zM1 26c0-7 13-7 13-2zM43 26c0-7-13-7-13-2z"/></svg>
  <b>60 +</b><small>Meetups</small>
</div>

<!-- WHAT WE DO -->
<section class="abs wwd"></section>
<h2 class="sec-title" style="top:2640px;color:var(--white)">What We Do</h2>
<div class="sec-rule" style="top:2702px;background:var(--white)"></div>

<div class="w-card" style="left:145px;top:2748px">
  <div class="w-copy"><h4>Nemo voluptatem</h4><p>Sed ut perspiciatis unde omnis iste natus voluptatem accusantium doloremque dantium, totam rem periam, eaque ipsa quae ab illo inventore veritatis et quasi</p></div>
  <div class="btn btn-line">Learn More</div>
  <div class="w-photo" role="img" aria-label="Blue-tinted photo of a team meeting with a cloud payment icon"><div class="w-ring"></div></div>
</div>
<div class="w-card" style="left:610px;top:2748px">
  <div class="w-copy"><h4>Nemo voluptatem</h4><p>Sed ut perspiciatis unde omnis iste natus voluptatem accusantium doloremque dantium, totam rem periam, eaque ipsa quae ab illo inventore veritatis et quasi</p></div>
  <div class="btn btn-line">Learn More</div>
  <div class="w-photo" role="img" aria-label="Blue-tinted photo of a person typing with a secure card icon"><div class="w-ring"></div></div>
</div>
<div class="w-card" style="left:145px;top:3043px">
  <div class="w-copy"><h4>Nemo voluptatem</h4><p>Sed ut perspiciatis unde omnis iste natus voluptatem accusantium doloremque dantium, totam rem periam, eaque ipsa quae ab illo inventore veritatis et quasi</p></div>
  <div class="btn btn-line">Learn More</div>
  <div class="w-photo" role="img" aria-label="Blue-tinted photo of documents with an invoice icon"><div class="w-ring"></div></div>
</div>
<div class="w-card" style="left:610px;top:3043px">
  <div class="w-copy"><h4>Nemo voluptatem</h4><p>Sed ut perspiciatis unde omnis iste natus voluptatem accusantium doloremque dantium, totam rem periam, eaque ipsa quae ab illo inventore veritatis et quasi</p></div>
  <div class="btn btn-line">Learn More</div>
  <div class="w-photo" role="img" aria-label="Blue-tinted photo of a workspace with an online payment icon"><div class="w-ring"></div></div>
</div>

<!-- NEWS -->
<h2 class="sec-title" style="top:3478px">Latest News</h2>
<div class="sec-rule" style="top:3542px"></div>

<article class="n-card" style="left:145px;top:3582px">
  <div class="n-photo" role="img" aria-label="Photo of two colleagues reviewing notes at a laptop" style="background:linear-gradient(135deg,#d8d2c8,#8f7f72 60%,#ece8e2)"></div>
  <div class="n-date"><span>&#9638;</span>FEB 3, 2021</div>
  <h5>Nemo enim ipsam volup quia voluptas sit</h5>
  <p>Sed ut perspiciatis unde omnis iste natus voluptatem accusantium domque laudantium, totam</p>
</article>
<article class="n-card" style="left:457px;top:3606px">
  <div class="n-photo" role="img" aria-label="Photo of a business presentation in a meeting room" style="background:linear-gradient(135deg,#4a5566,#9aa4b1 50%,#303946)"></div>
  <div class="n-date"><span>&#9638;</span>FEB 3, 2021</div>
  <h5>Nemo enim ipsam volup quia voluptas sit</h5>
  <p>Sed ut perspiciatis unde omnis iste natus voluptatem accusantium domque laudantium, totam</p>
</article>
<article class="n-card" style="left:769px;top:3582px">
  <div class="n-photo" role="img" aria-label="Photo of two consultants talking beside a laptop" style="background:linear-gradient(135deg,#6f8fb0,#c9a27c 55%,#e8dccd)"></div>
  <div class="n-date"><span>&#9638;</span>FEB 3, 2021</div>
  <h5>Nemo enim ipsam volup quia voluptas sit</h5>
  <p>Sed ut perspiciatis unde omnis iste natus voluptatem accusantium domque laudantium, totam</p>
</article>

<!-- FOOTER -->
<section class="abs footer"></section>

<!-- CTA -->
<svg class="abs cta" viewBox="0 0 1200 520" preserveAspectRatio="none" role="img" aria-label="Dark blue band over a faint office photo">
  <defs><linearGradient id="ctaBg" x1="0" y1="0" x2="1" y2="1"><stop offset="0" stop-color="#23357a"/><stop offset="1" stop-color="#1a2a63"/></linearGradient></defs>
  <path d="M0 0H1200V460C1080 420 960 380 780 410 600 440 500 500 320 480 180 465 80 440 0 450Z" fill="url(#ctaBg)"/>
</svg>
<h2 class="abs serif cta-title">Pay Management Consulting</h2>
<p class="abs cta-text">Sed ut perspiciatis unde omnis iste natus error sit voluptatem accusantium doloremque laudantium, totam rem aperiam, eaque ipsa Nemo enim ipsam voluptatem quia voluptas sit aspernatur aut odit aut fugit, sed quia consequuntur magni dolores</p>
<div class="btn btn-fill" style="left:487px;top:4420px;width:226px;height:42px">Get Started</div>

<div class="abs brand" style="left:137px;top:4688px;gap:6px">
  <span class="brand-dot" style="width:62px;height:62px;border-width:10px"></span><span class="brand-name" style="font-size:60px">Tally</span>
</div>
<p class="abs f-about">Nemo enim ipsam voluptatem quia voluptas sit aspernatur aut odit aut fugit, sed quia nsequuntur magni dolores eos qui ratione voluptatem sequi nesciunt.</p>
<div class="abs social" style="left:137px;top:4916px;gap:8px"><span style="width:30px;height:30px;border-radius:50%;border:2px solid var(--orange)"></span><span style="width:30px;height:30px;border-radius:50%;border:2px solid var(--orange)"></span><span style="width:30px;height:30px;border-radius:50%;border:2px solid var(--orange)"></span><span style="width:30px;height:30px;border-radius:50%;border:2px solid var(--orange)"></span></div>

<div class="abs f-head" style="left:382px;top:4682px">Sign Up for Newsletter</div>
<div class="field" style="top:4734px">Name *</div>
<div class="field" style="top:4790px">Email *</div>
<div class="field" style="top:4846px">Phone *</div>
<div class="btn btn-fill" style="left:382px;top:4916px;width:138px;height:42px;box-shadow:none">Submit</div>

<div class="abs f-head" style="left:700px;top:4684px">Contact Us</div>
<div class="abs f-contact">
  <div class="f-row"><svg width="16" height="20" viewBox="0 0 16 20" style="flex:none"><path d="M8 0a7 7 0 0 1 7 7c0 5-7 13-7 13S1 12 1 7a7 7 0 0 1 7-7z" fill="#e8703c"/><circle cx="8" cy="7" r="2.5" fill="#fff"/></svg><span>Tally Consulting<br>4210 Harbor Lane, Suite 8, Riverton</span></div>
  <div class="f-row"><span style="color:var(--orange)">&#9990;</span><span>Phone:<br>555-0199-9540</span></div>
  <div class="f-row"><span style="color:var(--orange)">&#9993;</span><span>Email:<br>hello@tallyconsult.example</span></div>
</div>

<div class="abs f-head" style="left:946px;top:4682px">Quick Links</div>
<div class="abs f-links">Home<br>About Us<br>Services<br>Blog<br>Resources<br>Contact us</div>

<div class="abs copy-rule"></div>
<p class="abs copyright">Tally Consulting © 2021 All Rights Reserved | Privacy Policy | Terms and Conditions</p>

</body>
</html>
```